website design Investment Fund

I am looking for a custom website that will work on desktop computer, tablet device and a cellular device. I have attached the booklet so you can get an idea of the look we are going for. Would like to use the website eventually for crowdfunding. We like the ski racer and mountain climbing designs.

Target Market(s)

Financial Services

Industry/Entity Type

Financial Service

Coding

Coded - Design and coding required

Number of Pages Required

5+ page

Font styles to use
Sans Serif

Requirements
Must have
• Must be viewable on a cell phone and tablet and desktop
Nice to have
• Contact us form

```html
<!DOCTYPE html>
<html lang="en">
<head>
<meta charset="utf-8">
<title>Vantor Ridge Fund</title>
<link href="https://fonts.googleapis.com/css2?family=Montserrat:wght@400;500;600;700&family=Lato:wght@400;700&family=Open+Sans:ital,wght@1,400&display=swap" rel="stylesheet">
<style>
:root{
  --red:#e2001a;
  --blue:#0f3c9c;
  --navy:#0b1f5c;
  --ink:#1d1d1f;
  --text:#3b3b3b;
  --muted:#6b6b6b;
  --field:#e6e6e6;
  --white:#ffffff;
}
*{box-sizing:border-box;margin:0;padding:0}
html,body{width:1200px;height:4950px;overflow:hidden;background:var(--white)}
body{font-family:"Lato",sans-serif;color:var(--text)}
.page{position:relative;width:1200px;height:4950px;overflow:hidden}
svg.layer{position:absolute;left:0;display:block}

/* header */
.site-header{position:absolute;top:0;left:0;width:1200px;height:113px;background:var(--white);border-top:4px solid var(--blue)}
.brand{position:absolute;left:137px;top:66px;display:flex;align-items:center;gap:10px;font-family:"Montserrat",sans-serif;font-weight:500;font-size:19px;color:var(--ink);letter-spacing:.3px}
.brand::before{content:"";width:14px;height:14px;background:var(--red)}
.contact-line{position:absolute;top:28px;right:140px;font-size:13px;color:#444;display:flex;gap:44px}
.contact-line span::before{content:"";display:inline-block;width:9px;height:9px;background:var(--red);border-radius:2px;margin-right:6px;vertical-align:0}
.main-nav{position:absolute;top:77px;right:138px;display:flex;gap:31px;font-family:"Montserrat",sans-serif;font-weight:600;font-size:12.5px;color:var(--ink)}

/* hero */
.hero-photo{position:absolute;top:113px;left:0;width:1200px;height:946px;background:linear-gradient(100deg,#3c4147 0%,#5b6670 32%,#7e98b3 55%,#b3c6d8 78%,#d9e2ea 100%)}
.hero-title{position:absolute;top:278px;right:138px;width:460px;text-align:right;font-family:"Montserrat",sans-serif;font-weight:700;font-size:35px;line-height:39px;color:var(--white);text-transform:uppercase}
.slide-arrow{position:absolute;top:392px;width:26px;height:50px}

/* about */
.mist{position:absolute;top:1500px;left:0;width:1200px;height:380px;background:linear-gradient(180deg,#fff 0%,#eef0f3 55%,#d9dee4 100%)}
.about-title{position:absolute;left:137px;top:1136px;font-family:"Montserrat",sans-serif;font-weight:600;font-size:28px;color:var(--ink)}
.about-sub{position:absolute;left:137px;top:1179px;font-family:"Montserrat",sans-serif;font-size:18px;color:var(--red)}
.about-copy{position:absolute;left:137px;top:1228px;width:575px;font-size:12.4px;line-height:23px;color:#444}
.about-copy-2{position:absolute;left:371px;top:1402px;width:320px;font-size:12.4px;line-height:23px;color:#444}
.about-mark{position:absolute;left:147px;top:1410px;width:195px;height:185px;background:linear-gradient(135deg,#dfe4ec,#c8d0dc)}
.btn-red{position:absolute;left:371px;top:1560px;width:118px;height:36px;background:var(--red);color:var(--white);font-family:"Montserrat",sans-serif;font-weight:700;font-size:11.5px;display:flex;align-items:center;justify-content:center;border-right:5px solid var(--blue)}

/* quick contact */
.quick-contact{position:absolute;left:750px;top:1106px;width:312px;height:500px;background:var(--white);box-shadow:0 3px 14px rgba(0,0,0,.18)}
.quick-contact svg{position:absolute;top:0;left:0}
.quick-contact h3{position:absolute;top:26px;width:100%;text-align:center;font-family:"Montserrat",sans-serif;font-weight:700;font-size:21px;color:var(--white)}
.field{position:absolute;left:22px;width:270px;height:35px;background:var(--field);border-left:4px solid var(--red);font-size:11.5px;color:#777;padding:11px 0 0 12px}
.submit{position:absolute;left:22px;top:425px;width:270px;height:42px;background:var(--red);border-right:5px solid var(--blue);color:var(--white);font-family:"Montserrat",sans-serif;font-weight:700;font-size:13px;display:flex;align-items:center;justify-content:center}

/* feature panels */
.panel{position:absolute;text-align:center;color:var(--white)}
.panel-icon{width:124px;height:124px;border-radius:50%;background:var(--white);margin:0 auto;display:flex;align-items:center;justify-content:center}
.panel-icon span{width:102px;height:102px;border-radius:50%;display:flex;align-items:center;justify-content:center;font-family:"Montserrat",sans-serif;font-weight:700;font-size:40px;color:var(--white)}
.panel h3{font-family:"Montserrat",sans-serif;font-weight:700;font-size:21px;line-height:26px;margin-top:20px;text-transform:uppercase}
.panel p{font-size:12.2px;line-height:21px;margin-top:18px}
.panel-next{width:38px;height:38px;border-radius:50%;background:var(--white);margin:32px auto 0;display:flex;align-items:center;justify-content:center}

/* team */
.team-title{position:absolute;top:2558px;width:1200px;text-align:center;font-family:"Montserrat",sans-serif;font-weight:600;font-size:28px;color:var(--ink)}
.team-sub{position:absolute;top:2601px;width:1200px;text-align:center;font-family:"Montserrat",sans-serif;font-size:18px;color:var(--red)}
.member{position:absolute;top:2684px;width:240px;text-align:center}
.member .photo{width:154px;height:154px;border-radius:50%;margin:0 auto;border:5px solid #dedede;background:linear-gradient(160deg,#c9ccd1,#8b9097)}
.member.lead .photo{border-color:var(--blue)}
.member .name{margin-top:18px;font-family:"Montserrat",sans-serif;font-weight:500;font-size:14.5px;color:var(--red);text-transform:uppercase}
.member .role{margin-top:6px;font-size:13px;color:var(--blue)}

/* quote */
.quote-mark{position:absolute;left:140px;top:3335px;font-family:"Montserrat",sans-serif;font-weight:700;font-size:150px;line-height:150px;color:var(--white)}
.quote-text{position:absolute;left:260px;top:3356px;width:485px;font-family:"Open Sans",sans-serif;font-style:italic;font-size:19px;line-height:28px;color:var(--white)}
.quote-author{position:absolute;left:260px;top:3538px;font-family:"Montserrat",sans-serif;font-weight:700;font-size:19px;color:var(--white)}

/* investors */
.invest-title{position:absolute;top:3864px;width:1200px;text-align:center;font-family:"Montserrat",sans-serif;font-weight:600;font-size:28px;color:var(--ink)}
.invest-photo{position:absolute;top:3961px;width:402px;height:318px;box-shadow:0 4px 14px rgba(0,0,0,.2)}
.invest-card{position:absolute;top:4154px;width:336px;height:230px;background:var(--white);box-shadow:0 4px 16px rgba(0,0,0,.16);padding:30px 0 0 28px}
.invest-card h4{font-family:"Montserrat",sans-serif;font-weight:600;font-size:21px;line-height:29px;color:var(--blue);text-transform:uppercase}
.invest-card .series{margin-top:16px;font-family:"Montserrat",sans-serif;font-weight:600;font-size:20px;color:var(--red)}
.invest-card .rate{margin-top:22px;font-family:"Montserrat",sans-serif;font-weight:500;font-size:19px;color:var(--ink)}
.invest-card .detail{margin-top:6px;font-family:"Montserrat",sans-serif;font-weight:600;font-size:13px;line-height:24px;color:#333;text-transform:uppercase}
.invest-card .detail b{text-transform:none}

/* footer */
.social{position:absolute;left:137px;top:4815px;display:flex;gap:6px}
.social span{width:30px;height:30px;border-radius:50%;border:2px solid var(--white)}
.copyright{position:absolute;left:137px;top:4864px;font-size:12px;line-height:20px;color:var(--white)}
</style>
</head>
<body>
<div class="page">

  <header class="site-header">
    <div class="brand">Vantor Ridge Fund</div>
    <div class="contact-line"><span>Email: hello@vantorridge.com</span><span>Phone: 1-800-555-0142</span></div>
    <nav class="main-nav"><span>COMPANY</span><span>OBJECTIVE</span><span>SERVICES</span><span>CLIENTS</span><span>LOAN PROGRAMS</span><span>FOLIO</span><span>CONTACT</span></nav>
  </header>

  <div class="hero-photo" role="img" aria-label="Rock climber scaling a cliff face above the clouds"></div>
  <svg class="layer" style="top:113px" width="1200" height="947" viewBox="0 113 1200 947">
    <polygon points="0,740 290,940 410,1022 1200,700 1200,1060 0,1060" fill="#fff"/>
    <polygon points="1200,540 1200,700 410,1022 290,940" fill="#e2001a"/>
    <polygon points="0,600 190,760 0,740" fill="#b8001a" opacity=".85"/>
    <polygon points="0,740 290,940 0,1058" fill="#0f3c9c"/>
  </svg>
  <h1 class="hero-title">Totally committed and focused on capital preservation and uninterrupted income forour investors</h1>
  <svg class="slide-arrow" style="left:42px" viewBox="0 0 26 50"><polyline points="24,2 2,25 24,48" fill="none" stroke="#fff" stroke-width="2"/></svg>
  <svg class="slide-arrow" style="left:1148px" viewBox="0 0 26 50"><polyline points="2,2 24,25 2,48" fill="none" stroke="#fff" stroke-width="2"/></svg>

  <div class="mist" role="img" aria-label="Misty mountain range fading into white"></div>
  <h2 class="about-title">ABOUT VANTOR RIDGE FUND</h2>
  <div class="about-sub">Arizona's Elite Boutique Lender</div>
  <p class="about-copy">Vantor Funding &amp; Investment, Inc. is a privately held mortgage lender, asset management and advisory firm headquartered in Scottsdale, Arizona which specializes in fast financing for debt, equity, mezzanine and land bank on real estate projects in the $100,000 to $50,000,000 range. As a highly reputable, successful and growth-focused company with decades of experience across the entire spectrum of real estate financing through Arizona, the Southwest United States and Mexico.</p>
  <div class="about-mark" role="img" aria-label="Brand artwork area"></div>
  <p class="about-copy-2">At Vantor, we've created an exceptional business focused on delivering privately funded financing to a wide range of clients. Our proven diligence, impeccable operating standards and expertise help to ensure that the funding process will run more rapidly and reliably than any other company in that market.</p>
  <div class="btn-red">READ MORE</div>

  <form class="quick-contact">
    <svg width="312" height="105" viewBox="0 0 312 105">
      <polygon points="0,0 312,0 312,72 156,100 0,72" fill="#e2001a"/>
      <polygon points="0,0 312,0 312,64 156,92 0,64" fill="#0f3c9c"/>
    </svg>
    <h3>QUICK CONTACT</h3>
    <div class="field" style="top:130px">Name:</div>
    <div class="field" style="top:177px">Email:</div>
    <div class="field" style="top:224px">Phone:</div>
    <div class="field" style="top:271px;height:130px">Message:</div>
    <div class="submit">SUBMIT HERE</div>
  </form>

  <svg class="layer" style="top:1813px" width="1200" height="606" viewBox="0 0 1200 606" role="img" aria-label="Ski racer and mountaineer photographs toned red and blue">
    <defs>
      <linearGradient id="redTone" x1="0" y1="0" x2="1" y2="1"><stop offset="0" stop-color="#e2001a"/><stop offset="1" stop-color="#c4001a"/></linearGradient>
      <linearGradient id="blueTone" x1="0" y1="0" x2="1" y2="1"><stop offset="0" stop-color="#0f3c9c"/><stop offset="1" stop-color="#1d4aa8"/></linearGradient>
    </defs>
    <polygon points="0,0 663,0 640,57 590,548 0,548" fill="url(#redTone)"/>
    <polygon points="558,57 1200,57 1200,606 631,606" fill="url(#blueTone)"/>
  </svg>
  <div class="panel" style="left:130px;top:1903px;width:420px">
    <div class="panel-icon"><span style="background:var(--blue)">$</span></div>
    <h3>The boutique fund<br>investors are looking for</h3>
    <p>The Fund Managers have decades of experience in private money lending as well as real estate investment, property and asset management, construction, and development. At vero eos lorem usamus et iusto odioignis simos ducimus qui blanditiisatum deleniti atquedolores et quas cimus qui loremoles.</p>
    <div class="panel-next"><svg width="16" height="12" viewBox="0 0 16 12"><path d="M1 6h13M9 1l5 5-5 5" fill="none" stroke="#e2001a" stroke-width="2"/></svg></div>
  </div>
  <div class="panel" style="left:662px;top:1961px;width:400px">
    <div class="panel-icon"><span style="background:var(--red)">$</span></div>
    <h3>Investment<br>strategy</h3>
    <p>The Fund Managers have decades of experience in private money lending as well as real estate investment, property and asset management, construction, and development. At vero eos lorem usamus et iusto odioignis simos ducimus qui blanditiisatum deleniti atquedolores et quas cimus qui loremoles.</p>
    <div class="panel-next"><svg width="16" height="12" viewBox="0 0 16 12"><path d="M1 6h13M9 1l5 5-5 5" fill="none" stroke="#0f3c9c" stroke-width="2"/></svg></div>
  </div>

  <h2 class="team-title">OUR TEAM</h2>
  <div class="team-sub">FOUNDING MEMBERS AND FUND MANAGERS</div>
  <div class="member lead" style="left:123px"><div class="photo" role="img" aria-label="Portrait of Martin D Vance"></div><div class="name">Martin D Vance</div><div class="role">Founder and Fund Manager</div></div>
  <div class="member" style="left:360px"><div class="photo" role="img" aria-label="Portrait of Diana Morrell"></div><div class="name">Diana Morrell</div><div class="role">Founder and Managing Partner</div></div>
  <div class="member" style="left:596px"><div class="photo" role="img" aria-label="Portrait of Theo Ranick"></div><div class="name">Theo Ranick</div><div class="role">Fund Advisor</div></div>
  <div class="member" style="left:833px"><div class="photo" role="img" aria-label="Portrait of Jack Jessup"></div><div class="name">Jack Jessup</div><div class="role">Chief Investment Officer</div></div>

  <svg class="layer" style="top:2860px" width="1200" height="1100" viewBox="0 2860 1200 1100" role="img" aria-label="Female climber on a rock face at sunset">
    <defs>
      <linearGradient id="dusk" x1="0" y1="0" x2="1" y2="1">
        <stop offset="0" stop-color="#9a958d"/><stop offset=".45" stop-color="#7a6650"/><stop offset=".8" stop-color="#4f3a2a"/><stop offset="1" stop-color="#3a2a20"/>
      </linearGradient>
    </defs>
    <polygon points="0,2865 308,3183 0,3230" fill="#e2001a"/>
    <polygon points="0,3230 1200,3057 1200,3596 0,3800" fill="url(#dusk)"/>
    <polygon points="885,3663 1200,3596 1200,3952" fill="#0f3c9c"/>
  </svg>
  <div class="quote-mark">“</div>
  <p class="quote-text">Sed ut perspiciatis unde omnis iste natus error sitolu ptatem accusantium doloremque laudantium, tota rem aperiam, eaque ipsa quae ab illo inventore verit atis et quasi architecto beatae vitae dicta sunt explica bo. Nemo enim ipsam voluptatem quia voluptait spernatur aut odit aut fugit, sed quia</p>
  <div class="quote-author">- Elena Ward, City Name</div>

  <h2 class="invest-title">ACCREDITED INVESTORS ONLY</h2>
  <div class="invest-photo" style="left:137px;background:linear-gradient(135deg,#f1f3f6,#c9ced6 60%,#8b95a3)" role="img" aria-label="Ski racer carving down a snowy slope"></div>
  <div class="invest-card" style="left:238px">
    <h4>Minimum investment<br>requirements</h4>
    <div class="series">SERIES A $50,000-$249,999</div>
    <div class="rate">RATE OF RETURN</div>
    <div class="detail">Series A 7% per annum<br><b>Term 24 months</b></div>
  </div>
  <div class="invest-photo" style="left:623px;background:linear-gradient(160deg,#2f5fae,#8ba6cf 55%,#e6ebf2)" role="img" aria-label="Mountaineer facing snowy peaks"></div>
  <div class="invest-card" style="left:725px">
    <h4>Minimum investment<br>requirements</h4>
    <div class="series">SERIES B $250,000.00</div>
    <div class="rate">RATE OF RETURN</div>
    <div class="detail">Series B 8% per annum<br><b>Term 24 months</b></div>
  </div>

  <svg class="layer" style="top:4470px" width="1200" height="480" viewBox="0 4470 1200 480" role="img" aria-label="Skier silhouette on a dark slope">
    <defs>
      <linearGradient id="night" x1="0" y1="0" x2="1" y2="1"><stop offset="0" stop-color="#1a2340"/><stop offset="1" stop-color="#3a3340"/></linearGradient>
    </defs>
    <polygon points="0,4538 183,4477 1200,4913 1200,4950 846,4950 0,4654" fill="#e2001a"/>
    <polygon points="0,4654 846,4950 0,4950" fill="#0f3c9c"/>
    <polygon points="0,4740 173,4673 788,4950 0,4950" fill="url(#night)"/>
  </svg>
  <div class="social"><span></span><span></span><span></span></div>
  <div class="copyright">© 2019 All Rights are Reserved.<br>Privacy Policy | Terms of Use | Site map</div>

</div>
</body>
</html>
```